Advanced Therapeutic Massage Therapist

I need a business card advertising my massage services as an advanced therapeutic massage therapist. I offer advanced therapeutic massage, swedish and deep tissue. I want to create a simple, professional and feminine card. I like bright colours and creativity.

I prefer a bold and experimental approach rather than something status-quo. A card to suggest therapeutic healing through dynamic massage. Motifs, shapes or layout which suggest movement and flow.
Updates

Target Market(s)

Everybody!

Industry/Entity Type

Health And Wellness

Contact Information for Business Card

The card should include:
My name, logo, services offered and my contact details.

Sláine Dunleavy
Massage Therapist

- Swedish - Deep Tissue - Advanced Therapeutic

Phone: (+353) 87 216 4093
Email: regenerate@slainedunleavy-example.com
Website: www.slainedunlevy-example.com

Font styles to use
Serif
Sans Serif
Decorative
Script

Colors

Designer to choose colors to be used in the design.

Requirements
Must have
• An example may contain something like this, yet concise:
• "Sláine Dunleavy
• Massage Therapist
• - Swedish - Deep Tissue - Advanced Therapeutic"
Nice to have
• This sentence is optional:
• Imagery such as a logo or symbol. I have attached a file containing a logo I had produced however the name is incorrect now as it is "Sláine" not "Nelly". It could be edited to change it to Sláine.
• I have sent the file as .psd .jpg. .pdf and .png
• I like when the card conveys energy, movement, pressure points, flow etc.
• I just like the designer to follow their own style and ideas. I like bright colours but must have a lot of a base colour to offset it. I really prefer them to follow their own inspiration. That is my preference.
Should not have
• Pine trees, non-native trees to Britain and Ireland, exotic flowers or animals that are not native to Britain and Ireland.
• I don't like brown as the background colour of the card.
• The cars shouldn't look like a wedding invitation i.e too many floral type designs.

```html
<!DOCTYPE html>
<html lang="en">
<head>
<meta charset="utf-8">
<title>Sláine Dunleavy – Business Card</title>
<link rel="stylesheet" href="https://fonts.googleapis.com/css2?family=Open+Sans:wght@400;600;700&display=swap">
<style>
  :root {
    --canvas-bg: #e9e7e3;
    --card-white: #ffffff;
    --card-black: #222223;
    --mint: #a8d3c9;
    --mint-soft: #cfe8e1;
    --bronze: #8b6a43;
    --gold: #c9a24a;
    --name-tone: #9a8566;
    --ink: #1c1c1c;
  }
  * { box-sizing: border-box; margin: 0; padding: 0; }
  html, body {
    width: 1200px;
    height: 900px;
    overflow: hidden;
    background: var(--canvas-bg);
    font-family: "Open Sans", sans-serif;
  }
  .card {
    position: absolute;
    left: 270px;
    width: 660px;
    height: 377px;
    overflow: hidden;
    box-shadow: 0 6px 18px rgba(0,0,0,0.18);
  }
  .card--front { top: 40px; background: var(--card-white); }
  .card--back {
    top: 475px;
    background:
      repeating-linear-gradient(0deg, rgba(255,255,255,0.035) 0 1px, transparent 1px 3px),
      var(--card-black);
  }

  /* front */
  .corner-mark {
    position: absolute;
    left: 0; top: 22px;
    width: 58px; height: 34px;
  }
  .identity { position: absolute; left: 72px; top: 18px; }
  .identity__name {
    font-size: 25px;
    font-weight: 700;
    color: var(--name-tone);
    letter-spacing: 0.2px;
    line-height: 1.1;
  }
  .identity__title {
    font-size: 17px;
    color: var(--ink);
    line-height: 1.2;
  }
  .contact { position: absolute; left: 28px; top: 142px; font-size: 17px; color: var(--ink); }
  .contact__row { display: flex; align-items: center; gap: 8px; line-height: 26px; }
  .contact__icon { width: 14px; height: 14px; flex: none; }
  .services { position: absolute; left: 28px; top: 212px; font-size: 18px; font-weight: 700; color: var(--ink); }
  .services__row { display: flex; align-items: center; gap: 6px; line-height: 26px; }
  .services__dot {
    width: 11px; height: 11px; border-radius: 50%;
    background: radial-gradient(circle at 35% 35%, var(--mint-soft), var(--bronze));
    flex: none;
  }
  .services__row .services__dot + span + .services__dot { margin-left: 2px; }
  .footer-band { position: absolute; left: 0; bottom: 0; width: 660px; height: 62px; }

  .emblem {
    position: absolute;
    border-radius: 50%;
    background: radial-gradient(circle at 45% 45%, #d6ece6 0%, var(--mint) 60%, #8fc0b4 100%);
    border: 3px solid var(--gold);
    box-shadow: 0 0 0 6px rgba(201,162,74,0.25);
  }
  .emblem--front { left: 420px; top: 105px; width: 176px; height: 176px; }
  .emblem--back { left: 240px; top: 98px; width: 180px; height: 180px; }
</style>
</head>
<body>

<section class="card card--front" aria-label="Business card front">
  <svg class="corner-mark" viewBox="0 0 58 34" aria-hidden="true">
    <defs>
      <linearGradient id="markGrad" x1="0" y1="0" x2="1" y2="0">
        <stop offset="0" stop-color="#ffffff"/>
        <stop offset="1" stop-color="#8b6a43"/>
      </linearGradient>
    </defs>
    <polygon points="0,34 30,0 58,0 58,34" fill="url(#markGrad)"/>
  </svg>

  <header class="identity">
    <h1 class="identity__name">Sláine Dunleavy</h1>
    <p class="identity__title">Massage Therapist</p>
  </header>

  <div class="contact">
    <p class="contact__row">
      <svg class="contact__icon" viewBox="0 0 24 24" aria-hidden="true"><path fill="#8b6a43" d="M6.6 10.8a15 15 0 0 0 6.6 6.6l2.2-2.2c.3-.3.7-.4 1-.2 1.1.4 2.3.6 3.6.6.6 0 1 .4 1 1V20c0 .6-.4 1-1 1A17 17 0 0 1 3 4c0-.6.4-1 1-1h3.5c.6 0 1 .4 1 1 0 1.3.2 2.5.6 3.6.1.3 0 .7-.2 1z"/></svg>
      <span>(+353) 87 216 4093</span>
    </p>
    <p class="contact__row">
      <svg class="contact__icon" viewBox="0 0 24 24" aria-hidden="true"><rect x="2" y="5" width="20" height="14" rx="1" fill="#8b6a43"/><path d="M2 6l10 7 10-7" fill="none" stroke="#cfe8e1" stroke-width="1.6"/></svg>
      <span>slainemassage@example-mail.com</span>
    </p>
  </div>

  <ul class="services">
    <li class="services__row"><span class="services__dot"></span><span>Swedish</span><span class="services__dot"></span><span>Deep Tissue</span></li>
    <li class="services__row"><span class="services__dot"></span><span>Advanced Therapeutic</span></li>
  </ul>

  <div class="emblem emblem--front" role="img" aria-label="Circular tree of life emblem in gold on soft mint"></div>

  <svg class="footer-band" viewBox="0 0 660 62" aria-hidden="true">
    <defs>
      <linearGradient id="bandGrad" x1="0" y1="0" x2="0" y2="1">
        <stop offset="0" stop-color="#a8d3c9"/>
        <stop offset="1" stop-color="#8b6a43"/>
      </linearGradient>
    </defs>
    <rect x="0" y="0" width="660" height="62" fill="url(#bandGrad)"/>
    <polygon points="268,62 280,62 302,0 290,0" fill="#ffffff"/>
  </svg>
</section>

<section class="card card--back" aria-label="Business card back">
  <div class="emblem emblem--back" role="img" aria-label="Circular tree of life emblem in gold on soft mint"></div>
</section>

</body>
</html>
```